Wandering Rooms Stationary Set

Wandering Rooms is a bespoke interior design firm set to provide services to VIP clients with elegance and minimalism is the main theme for our stationary set. We require a full stationary set covering A4 letterhead, A4 & A3 envelopes, business cards, USB's, CDs, email signature and any other item the designer sees fit. logo is already designed and finalized, and we require the designer to use it as is without modifying the logo.

Address to be used on letterhead / business cards ...etc shall be as follows:

Phone : +971 2 518 2047
P.O. Box : 309186
Address: Block C&D, Bldg. 47, Court 12, Abu Dhabi, United Arab Emirates
Website: www.wanderingrooms-example.com

Target Market(s)

VIP Clients

Industry/Entity Type

Interior Design

Font styles to use
Other font styles liked:
• something to be unique

Colors

Designer to choose colors to be used in the design.

Requirements
Must have
• Elegant, minimalistic
Nice to have
• Simple yet elegant design having a sharp yet clean cut format
Should not have
• No additional colours, just colours that are used in the logo (silver, black or gold)

```html
<!DOCTYPE html>
<html lang="en">
<head>
<meta charset="utf-8">
<title>Wandering Rooms – Letterhead</title>
<link href="https://fonts.googleapis.com/css2?family=Arimo:wght@400&display=swap" rel="stylesheet">
<style>
  :root {
    --backdrop: #5b5b5b;
    --paper: #ffffff;
    --ink: #1c1c1c;
    --ink-soft: #3a3a3a;
    --gold: #c9953f;
  }
  * { margin: 0; padding: 0; box-sizing: border-box; }
  html, body {
    width: 1200px;
    height: 1038px;
    overflow: hidden;
    background: var(--backdrop);
  }
  .stage {
    width: 1200px;
    height: 1038px;
    display: flex;
    align-items: center;
    justify-content: center;
  }
  .letterhead {
    position: relative;
    width: 690px;
    height: 976px;
    background: var(--paper);
    font-family: "Arimo", Arial, sans-serif;
    color: var(--ink);
  }
  .brand {
    position: absolute;
    top: 64px;
    left: 64px;
    display: flex;
    align-items: center;
    gap: 10px;
  }
  .brand-dot {
    width: 8px;
    height: 8px;
    border-radius: 50%;
    background: var(--gold);
  }
  .brand-name {
    font-size: 17px;
    font-weight: 400;
    letter-spacing: 0.28em;
    text-transform: uppercase;
    color: var(--ink);
  }
  .footer {
    position: absolute;
    left: 64px;
    bottom: 48px;
    display: flex;
    align-items: stretch;
    gap: 9px;
  }
  .footer-rule {
    width: 3px;
    background: var(--gold);
  }
  .footer-lines {
    font-size: 9.5px;
    line-height: 1.35;
    color: var(--ink-soft);
  }
</style>
</head>
<body>
  <main class="stage">
    <article class="letterhead">
      <header class="brand">
        <span class="brand-dot"></span>
        <span class="brand-name">Wandering Rooms</span>
      </header>
      <footer class="footer">
        <span class="footer-rule"></span>
        <address class="footer-lines" style="font-style: normal;">
          <div>Block C&amp;D, Bldg. 47, Court 12, Abu Dhabi, United Arab Emirates</div>
          <div>P.O. Box: 309186 · Tel: +971 2 518 2047 · www.wanderingrooms-example.com</div>
        </address>
      </footer>
    </article>
  </main>
</body>
</html>
```